Hollendorf Business Card

This is the personal business card for Dr Mark Hollendorf and convers three area of his professional activity - all of them involve (foreign) languages:
o QRVB International Ltd - A translation company with 50 staff. Trades internationally
o WideHarbor Ltd - a global online auction marketplace for translation services (startup)
o Tonal Mosaic - cutting edge technology from the brain sciences which helps learners assimilate the sound patterns of a new language (startup)

Target Market(s)

The card needs to have a "cutting edge" feel - but for a fairly conservative audience - academics, investors.

Industry/Entity Type

Business

Requirements
Must have
• Text:
Dr Mark Hollendorf

Co-founder QRVB International Ltd (Language translation)
Founder WideHarbor Ltd (Translation marketplace)
Founder Tonal Mosaic (Language acquisition)

email: mark.oswin@velmora.co.nz
Phone: +64 21 596 3172
Twitter: @MarkOswin7

```html
<!DOCTYPE html>
<html lang="en">
<head>
<meta charset="utf-8">
<title>Dr Mark Hollendorf – Business Card</title>
<link rel="stylesheet" href="https://fonts.googleapis.com/css2?family=Courier+Prime:wght@400;700&family=Cabin:wght@400&display=swap">
<style>
  :root {
    --card-bg: #ffffff;
    --ink: #111111;
    --badge: #000000;
    --badge-text: #ffffff;
    --accent: #c8673a;
  }
  html, body {
    margin: 0;
    padding: 0;
    overflow: hidden;
    background: var(--card-bg);
  }
  .card {
    position: relative;
    width: 1200px;
    height: 686px;
    background: var(--card-bg);
    overflow: hidden;
    color: var(--ink);
    font-family: "Cabin", "Gill Sans", sans-serif;
  }
  .accent-bar {
    position: absolute;
    left: 525px;
    top: 41px;
    width: 50px;
    height: 645px;
    background: var(--accent);
  }
  .name-badge {
    position: absolute;
    left: 35px;
    top: 46px;
    width: 551px;
    height: 156px;
  }
  .name-badge svg { display: block; }
  .name-badge__text {
    position: absolute;
    inset: 0;
    display: flex;
    align-items: center;
    justify-content: center;
    font-family: "Courier Prime", "Courier New", monospace;
    font-size: 40px;
    color: var(--badge-text);
    white-space: nowrap;
  }
  .details {
    position: absolute;
    left: 628px;
    top: 0;
    width: 560px;
  }
  .details__name {
    position: absolute;
    top: 66px;
    margin: 0;
    font-family: "Courier Prime", "Courier New", monospace;
    font-weight: 400;
    font-size: 36px;
    line-height: 42px;
    white-space: nowrap;
  }
  .details__profession {
    position: absolute;
    top: 134px;
    margin: 0;
    font-size: 32px;
    line-height: 38px;
    white-space: nowrap;
  }
  .ventures {
    position: absolute;
    top: 279px;
    margin: 0;
    padding: 0;
    list-style: none;
    font-size: 25px;
    line-height: 33px;
    width: 530px;
  }
  .ventures li { margin-bottom: 23px; }
  .contact {
    position: absolute;
    top: 482px;
    margin: 0;
    font-size: 30px;
    line-height: 42px;
    font-style: normal;
    white-space: nowrap;
  }
</style>
</head>
<body>
  <div class="card">
    <div class="accent-bar"></div>

    <div class="name-badge">
      <svg width="551" height="156" viewBox="0 0 551 156" aria-hidden="true">
        <ellipse cx="275.5" cy="78" rx="275.5" ry="78" fill="var(--badge)"/>
      </svg>
      <div class="name-badge__text">Dr. Mark Hollendorf</div>
    </div>

    <div class="details">
      <h1 class="details__name">Mark Hollendorf</h1>
      <p class="details__profession">Profession in Foreign Languages</p>

      <ul class="ventures">
        <li>Co-founder QRVB International Ltd (Language Translation)</li>
        <li>Founder WideHarbor Ltd (Translation Marketplace)</li>
        <li>Founder Tonal Mosaic (Language Acquisition)</li>
      </ul>

      <address class="contact">
        Phone: +64 21 596 3172<br>
        Twitter: @MarkOswin7<br>
        E-mail: mark.oswin@velmora.co.nz
      </address>
    </div>
  </div>
</body>
</html>
```